Vantiqo custom business card design

Need a authentic, innovative business card design for a new mobile app business. I am uploading a few screen images from our app for you to view. I would like app design theme to match business card design. I can also send logo images.

```html
<!DOCTYPE html>
<html lang="en">
<head>
<meta charset="utf-8">
<title>Vantiqo Business Card</title>
<link rel="stylesheet" href="https://fonts.googleapis.com/css2?family=Montserrat:wght@800&family=Lato:wght@300;400&display=swap">
<style>
  :root {
    --stage: #2e2e2f;
    --card: #1c1d1f;
    --card-back: #161718;
    --pattern-top: #26272a;
    --pattern-bottom: #1a1b1d;
    --purple: #5e1a91;
    --white: #ffffff;
    --text-light: #e6e6e6;
    --text-muted: #a9a9ab;
    --rule: #6b6b6e;
  }
  html, body {
    margin: 0;
    padding: 0;
    width: 1200px;
    height: 1108px;
    overflow: hidden;
    background: var(--stage);
  }
  .stage {
    position: relative;
    width: 1200px;
    height: 1108px;
  }
  .card {
    position: absolute;
    top: 234px;
    width: 400px;
    height: 640px;
    border-radius: 26px;
    overflow: hidden;
    box-shadow: 0 18px 40px rgba(0,0,0,0.45);
  }
  .card--front {
    left: 170px;
    background: var(--card);
    text-align: center;
    color: var(--text-light);
    font-family: "Lato", sans-serif;
  }
  .card--back {
    left: 630px;
    background: var(--card-back);
  }
  .brand-dot {
    display: block;
    width: 170px;
    height: 170px;
    margin: 54px auto 0;
    border-radius: 50%;
    background: var(--purple);
  }
  .brand-name {
    font-family: "Montserrat", sans-serif;
    font-weight: 800;
    color: var(--white);
    letter-spacing: 0.5px;
    margin: 0;
  }
  .card--front .brand-name {
    font-size: 56px;
    line-height: 1;
    margin-top: 26px;
  }
  .person-name {
    margin: 34px 0 0;
    font-size: 24px;
    font-weight: 400;
    letter-spacing: 0.5px;
    color: var(--white);
  }
  .person-role {
    margin: 4px 0 0;
    font-size: 17px;
    font-weight: 300;
    color: var(--text-muted);
  }
  .icon-rule {
    display: flex;
    align-items: center;
    justify-content: center;
    gap: 8px;
    margin: 12px 70px 0;
  }
  .icon-rule::before, .icon-rule::after {
    content: "";
    flex: 1;
    height: 1px;
    background: var(--rule);
  }
  .icon-rule svg { width: 20px; height: 20px; }
  .contact {
    list-style: none;
    margin: 10px 0 0;
    padding: 0;
    font-size: 19px;
    line-height: 1.35;
    color: var(--text-light);
  }
  .divider {
    width: 260px;
    height: 1px;
    background: var(--rule);
    margin: 12px auto 10px;
  }
  .address {
    margin: 0;
    font-style: normal;
    font-size: 19px;
    line-height: 1.35;
    color: var(--text-light);
  }
  .back-pattern {
    position: absolute;
    inset: 0 0 180px 0;
    background: linear-gradient(180deg, var(--pattern-top), var(--pattern-bottom));
  }
  .card--back .brand-name {
    position: absolute;
    left: 48px;
    bottom: 86px;
    font-size: 76px;
    line-height: 1;
  }
</style>
</head>
<body>
<main class="stage">
  <section class="card card--front" aria-label="Business card front">
    <span class="brand-dot" aria-hidden="true"></span>
    <h1 class="brand-name">Vantiqo</h1>
    <p class="person-name">MARCUS HALE</p>
    <p class="person-role">Managing Director</p>
    <div class="icon-rule" aria-hidden="true">
      <svg viewBox="0 0 20 20"><circle cx="10" cy="10" r="9.5" fill="#fff"/><path d="M7 5.5l1.6 1.6-1 1.2a6 6 0 0 0 3.1 3.1l1.2-1 1.6 1.6-1.2 1.5C9.5 13.3 6.7 10.5 5.5 7.5z" fill="#1c1d1f"/></svg>
      <svg viewBox="0 0 20 20"><circle cx="10" cy="10" r="9.5" fill="#fff"/><rect x="5" y="6.5" width="10" height="7" fill="none" stroke="#1c1d1f" stroke-width="1.4"/><path d="M5 6.5l5 4 5-4" fill="none" stroke="#1c1d1f" stroke-width="1.4"/></svg>
      <svg viewBox="0 0 20 20"><circle cx="10" cy="10" r="9.5" fill="#fff"/><circle cx="10" cy="10" r="5" fill="none" stroke="#1c1d1f" stroke-width="1.3"/><path d="M5 10h10M10 5c-2.4 2.8-2.4 7.2 0 10M10 5c2.4 2.8 2.4 7.2 0 10" fill="none" stroke="#1c1d1f" stroke-width="1.1"/></svg>
    </div>
    <ul class="contact">
      <li>444 555 7120</li>
      <li>hello@vantiqo.app</li>
      <li>www.vantiqo.app</li>
    </ul>
    <div class="divider"></div>
    <address class="address">87, Harbor Lane West,<br>Northvale, 20318</address>
  </section>

  <section class="card card--back" aria-label="Business card back">
    <div class="back-pattern" role="img" aria-label="Tonal repeat pattern of the brand symbol fading toward the bottom"></div>
    <p class="brand-name">Vantiqo</p>
  </section>
</main>
</body>
</html>
```